Friendly website/webshop needed for small family store

Hello .. I really need a website that is easy to use as I have no experience with this at all. ..
My shop is called quillmoss and I had a fantastic logo from craft forge - I asked for something mid century modern and I love it. I will attach . There might be some development around the logo now for various paraphernalia ( stickers , printed tissue paper carrier bags etc.. ) I would also like some sort of help with a slogan such as 'sing your prettiest song' as in,  live your best life etc..  but I'm not sure if this is a little trite .... ? but it would be nice to link the quillmoss with a little Motto.    If I need to pay extra for this - please could you let me know ... I'm happy to add on payment ..
As you can see the only LOGO colours really are grey black and orange .. so I would like some ideas to expand on the bird  to bring in some more colours.....  the tag line flower.children.home I would like to drop..
* the original brief included flowers on the tag line  because at the time we were also a florist . we now just sell dried flowers
My shop is in the beautiful town of Malvern, we have lots of tourist that come to walk the hills and enjoy nature - it's a family and dog friendly sort of town and we are a dog and family friendly sort of shop :-) It's a relaxed space that focuses on beautiful handmade items such as baskets & wooden utensils  from Africa, textiles from India and ceramics from France, Portugal and Italy.  We have a lovely section for children that sells beautiful soft toys from Charmel Duvo and the wonderful mice family and bunnies from Tornby.
We stock OBRETI homeware which is lovely and earthy and natural.
We would like to communicate the value of buying thoughtfully  and conscientiously, of building a beautiful home whilst investing in & supporting makers world wide. We don't sell anything that can't be repurposed, recycled etc..
Thank you

```html
<!DOCTYPE html>
<html lang="en">
<head>
<meta charset="utf-8">
<title>quillmoss — Live Your Best Life</title>
<link rel="stylesheet" href="https://fonts.googleapis.com/css2?family=Righteous&family=Jost:wght@400;500;600&display=swap">
<style>
:root{
  --terracotta:#c9857a;
  --terracotta-deep:#b9705f;
  --sky:#6fa7b8;
  --slate:#6f7b98;
  --ink:#1f1f1f;
  --text:#555;
  --mist:#eef0f4;
  --footer:#2b2b2c;
  --white:#fff;
  --star:#f4a21e;
}
*{box-sizing:border-box;margin:0;padding:0}
html,body{width:1200px;height:4231px;overflow:hidden}
body{position:relative;background:var(--white);font-family:'Jost',sans-serif;color:var(--text)}
.abs{position:absolute}
.display{font-family:'Righteous',sans-serif;color:var(--ink);font-weight:400}
.btn{position:absolute;display:flex;align-items:center;justify-content:center;border-radius:20px;font-family:'Jost',sans-serif;font-weight:500;font-size:16px;color:var(--ink);height:40px;width:150px}
.btn-sky{background:var(--sky)}
.btn-slate{background:var(--slate)}
/* header */
.header{position:absolute;left:0;top:0;width:1200px;height:164px;background:var(--white);border-top:3px solid var(--sky)}
.brand{position:absolute;left:110px;top:60px;text-align:left}
.brand-mark{position:absolute;left:150px;top:18px;width:46px;height:46px;border-radius:50%;background:var(--sky)}
.brand-name{font-family:'Jost',sans-serif;font-weight:600;font-size:34px;color:var(--ink);line-height:1}
.brand-slogan{font-family:'Jost',sans-serif;font-weight:600;font-size:13px;color:var(--terracotta);letter-spacing:.5px;margin-top:4px}
.contact-item{position:absolute;top:31px;display:flex;align-items:center;gap:20px}
.icon-dot{width:52px;height:52px;border-radius:50%;background:var(--sky);display:flex;align-items:center;justify-content:center}
.contact-label{font-size:12px;color:#777}
.contact-value{font-size:18px;color:#333;margin-top:4px}
.nav{position:absolute;left:279px;top:112px;width:921px;height:52px;background:var(--terracotta);clip-path:polygon(14px 0,100% 0,100% 100%,0 100%)}
.nav a{position:absolute;top:17px;font-size:13px;color:var(--white);text-decoration:none}
.nav .nav-cta{top:14px;background:var(--sky);color:var(--ink);border-radius:14px;padding:3px 22px;font-weight:500}
/* hero */
.hero{position:absolute;left:0;top:164px;width:1200px;height:660px}
.hero-title{position:absolute;left:0;top:290px;width:1200px;text-align:center;font-size:78px;color:var(--white)}
.hero-sub{position:absolute;left:0;top:390px;width:1200px;text-align:center;font-size:19px;line-height:37px;color:var(--white)}
/* sections */
.section-title{position:absolute;left:0;width:1200px;text-align:center;font-size:44px}
.about-blob{left:90px;top:968px;width:521px;height:595px;background:var(--mist);border-radius:20px 260px 260px 260px}
.about-photo{left:112px;top:992px;width:479px;height:546px;border-radius:10px 240px 240px 240px;background:linear-gradient(135deg,#8b7a68,#c8b49c 55%,#6d5e4e)}
.about-title{left:665px;top:1036px;font-size:42px}
.about-copy{left:665px;top:1110px;width:430px;font-size:16px;line-height:34px}
.about-copy p+p{margin-top:34px}
.lead{top:1745px;left:0;width:1200px;text-align:center;font-size:16px;line-height:34px}
.product-card{position:absolute;top:1847px;width:233px;height:369px;background:var(--white);border-radius:10px;box-shadow:0 2px 12px rgba(0,0,0,.08);text-align:center}
.product-img{margin:18px auto 0;width:198px;height:229px;border-radius:16px}
.product-name{font-size:17px;color:#333;margin-top:22px}
.product-price{font-size:16px;color:#222;margin-top:6px}
.product-link{font-size:11px;color:var(--slate);text-decoration:underline;margin-top:6px;display:block}
/* testimonials */
.reviews{position:absolute;left:0;top:2421px;width:1200px;height:580px;background:linear-gradient(90deg,#b26f62,#c9857a 40%,#c9857a);overflow:hidden}
.reviews-title{top:88px;color:var(--white)}
.review-card{position:absolute;top:159px;width:315px;height:347px;background:var(--white);border-radius:30px 50px 30px 50px;padding:30px 30px 0 32px}
.stars{color:var(--star);font-size:16px;letter-spacing:3px}
.review-text{font-size:12.5px;line-height:28.4px;color:#555;margin-top:8px}
.review-foot{position:absolute;left:32px;right:30px;top:266px;border-top:1px solid #e4e4e4;padding-top:14px;display:flex;align-items:center;gap:12px}
.avatar{width:38px;height:38px;border-radius:50%;background:#8a8f99}
.reviewer{font-size:12px;color:#222;font-weight:600}
.reviewer small{display:block;font-weight:400;color:#777;font-size:11px}
.badge{margin-left:auto;width:28px;height:28px;border-radius:50%;border:4px solid #8aa7c7}
.arrow{position:absolute;left:65px;width:40px;height:40px;border-radius:50%;display:flex;align-items:center;justify-content:center}
/* blog */
.blog-card{position:absolute;top:3185px;width:315px;height:487px;background:var(--white);border-radius:8px;box-shadow:0 2px 10px rgba(0,0,0,.06);text-align:center}
.blog-img{width:315px;height:230px;border-radius:8px 8px 0 0}
.blog-head{font-weight:600;font-size:13.5px;line-height:26px;color:#222;margin-top:30px;padding:0 30px;text-transform:uppercase}
.blog-body{font-size:12.5px;line-height:27px;color:#666;margin-top:10px;padding:0 22px}
.blog-link{display:block;font-size:12px;color:var(--slate);text-decoration:underline;margin-top:8px}
/* footer */
.footer{position:absolute;left:0;top:3850px;width:1200px;height:320px;background:var(--footer)}
.footer-name{position:absolute;left:135px;top:180px;font-size:46px;font-weight:600;color:#4a4a4c;line-height:1}
.footer-slogan{position:absolute;left:135px;top:245px;font-size:22px;font-weight:600;color:var(--terracotta);letter-spacing:1px}
.footer-col{position:absolute;top:68px;color:var(--white)}
.footer-col h4{font-family:'Righteous',sans-serif;font-weight:400;font-size:22px;margin-bottom:14px}
.footer-col li{list-style:none;font-size:13px;line-height:33.5px}
.field{width:197px;height:36px;border-radius:18px;background:var(--white);font-size:11px;color:#666;padding:11px 28px;margin-top:18px}
.subscribe{width:197px;height:36px;border-radius:18px;background:var(--terracotta);font-size:11px;color:var(--white);display:flex;align-items:center;justify-content:center;margin-top:14px}
.bottom-bar{position:absolute;left:0;top:4170px;width:1200px;height:61px;background:var(--sky)}
.social{position:absolute;top:18px;width:26px;height:26px;border-radius:50%;background:var(--white)}
</style>
</head>
<body>

<header class="header">
  <div class="brand-mark abs" style="left:112px;top:20px;width:40px;height:40px;border-radius:50%;background:var(--sky)"></div>
  <div class="brand abs" style="left:112px;top:96px">
    <div class="brand-name">quillmoss</div>
    <div class="brand-slogan">LIVE YOUR BEST LIFE</div>
  </div>

  <div class="contact-item" style="left:412px">
    <div class="icon-dot"><svg width="20" height="20" viewBox="0 0 24 24"><path fill="#fff" d="M6.6 10.8a15 15 0 0 0 6.6 6.6l2.2-2.2c.3-.3.7-.4 1-.2 1.1.4 2.3.6 3.6.6.6 0 1 .4 1 1V20c0 .6-.4 1-1 1A17 17 0 0 1 3 4c0-.6.4-1 1-1h3.5c.6 0 1 .4 1 1 0 1.3.2 2.5.6 3.6.1.3 0 .7-.2 1z"/></svg></div>
    <div><div class="contact-label">Call Us:</div><div class="contact-value">+1 555 014 2290</div></div>
  </div>
  <div class="contact-item" style="left:692px">
    <div class="icon-dot"><svg width="20" height="16" viewBox="0 0 24 18"><rect x="1" y="1" width="22" height="16" rx="2" fill="#fff"/><path d="M2 3l10 7 10-7" stroke="#6fa7b8" stroke-width="2" fill="none"/></svg></div>
    <div><div class="contact-label">Email Us:</div><div class="contact-value">hello@quillmoss-shop.com</div></div>
  </div>
  <div class="icon-dot abs" style="left:970px;top:31px"><svg width="16" height="18" viewBox="0 0 16 18"><circle cx="8" cy="5" r="4" fill="#fff"/><path d="M1 18c0-5 3-7 7-7s7 2 7 7z" fill="#fff"/></svg></div>
  <div class="icon-dot abs" style="left:1034px;top:31px"><svg width="20" height="18" viewBox="0 0 20 18"><path d="M1 1h3l2 10h11l2-7H5" stroke="#fff" stroke-width="2" fill="none"/><circle cx="8" cy="15" r="1.8" fill="#fff"/><circle cx="16" cy="15" r="1.8" fill="#fff"/></svg></div>

  <nav class="nav">
    <a style="left:38px">Home</a>
    <a style="left:130px">About Us</a>
    <a style="left:245px">Our Products</a>
    <a style="left:381px">Testimonials</a>
    <a style="left:510px">Blog</a>
    <a style="left:595px">Contact Us</a>
    <a class="nav-cta" style="left:688px">Get Started</a>
  </nav>
</header>

<section class="hero">
  <svg class="abs" style="left:0;top:0" width="1200" height="660" viewBox="0 0 1200 660">
    <defs>
      <linearGradient id="heroShade" x1="0" y1="0" x2="1" y2="1">
        <stop offset="0" stop-color="#4b4036"/><stop offset=".5" stop-color="#6e5c4a"/><stop offset="1" stop-color="#3f352c"/>
      </linearGradient>
    </defs>
    <path d="M0 0H1200V570Q600 700 0 570Z" fill="#6fa7b8"/>
    <path d="M0 0H1200V555Q600 680 0 555Z" fill="#c9857a"/>
    <path role="img" aria-label="Interior of the shop with woven baskets, shelves and plants" d="M0 0H1200V545Q600 665 0 545Z" fill="url(#heroShade)"/>
  </svg>
  <h1 class="hero-title display">Welcome To quillmoss</h1>
  <p class="hero-sub">Sed ut perspiciatis unde omnis iste natus error sit voluptatem accusantium doloremque<br>laudantium, totam rem aperiam, eaque ipsa quae ab illo inventore veritatis</p>
  <div class="btn btn-sky" style="left:442px;top:481px">Get Started</div>
  <div class="btn btn-slate" style="left:607px;top:481px">Contact Us</div>
</section>

<section class="about">
  <div class="abs about-blob"></div>
  <div class="abs about-photo" role="img" aria-label="Children's corner with soft toy mice, macarons and gifts on a woven mat"></div>
  <h2 class="abs display about-title">About Us</h2>
  <div class="abs about-copy">
    <p>I must explain to you how all this mistaken idea of denouncing pleasure and praising pain was born and I will give you a complete account of the system, and expound the actual teachings of the great explorer of the truth, the master-builder of human happiness.</p>
    <p>No one rejects, dislikes, or avoids pleasure itself, because it is pleasure, but because those who do not know how to pursue pleasure rationally encounter</p>
  </div>
  <div class="btn btn-slate" style="left:665px;top:1443px">Read More</div>
</section>

<section class="products">
  <h2 class="section-title display" style="top:1676px">Our Products</h2>
  <p class="abs lead">I must explain to you how all this mistaken idea of denouncing pleasure and praising pain was born and I will give<br>you a complete account of the system, and expound the actual teachings of the great explorer</p>

  <div class="product-card" style="left:97px">
    <div class="product-img" role="img" aria-label="Stacked woven baskets beside a palm" style="background:linear-gradient(160deg,#7d8a5b,#b58a66 60%,#8a6a52)"></div>
    <div class="product-name">Baskets</div><div class="product-price">Amount: $45.00</div><a class="product-link">View Products</a>
  </div>
  <div class="product-card" style="left:355px">
    <div class="product-img" role="img" aria-label="Brown plush teddy bear soft toy" style="background:linear-gradient(160deg,#c79a78,#7a4a30 60%,#d9b79a)"></div>
    <div class="product-name">Soft Toys</div><div class="product-price">Amount: $45.00</div><a class="product-link">View Products</a>
  </div>
  <div class="product-card" style="left:611px">
    <div class="product-img" role="img" aria-label="Stack of carved wooden plates" style="background:linear-gradient(180deg,#e8e2dc,#b98a68 60%,#8c5f42)"></div>
    <div class="product-name">Wooden Utensils</div><div class="product-price">Amount: $45.00</div><a class="product-link">View Products</a>
  </div>
  <div class="product-card" style="left:868px">
    <div class="product-img" role="img" aria-label="Hand-painted floral ceramic plate" style="background:radial-gradient(circle at 55% 50%,#e9eef2,#3d5f9a 55%,#6d6e70)"></div>
    <div class="product-name">Ceramics</div><div class="product-price">Amount: $45.00</div><a class="product-link">View Products</a>
  </div>

  <div class="btn btn-sky" style="left:442px;top:2265px">View More</div>
  <div class="btn btn-slate" style="left:607px;top:2265px">Contact Us</div>
</section>

<section class="reviews">
  <h2 class="section-title display reviews-title">Our Happy Customers</h2>

  <div class="arrow" style="top:287px;background:#3f6f8a"><svg width="10" height="12" viewBox="0 0 10 12"><path d="M7 1L2 6l5 5" stroke="#fff" stroke-width="2" fill="none"/></svg></div>
  <div class="arrow" style="top:337px;background:#e9e9e9"><svg width="10" height="12" viewBox="0 0 10 12"><path d="M3 1l5 5-5 5" stroke="#999" stroke-width="2" fill="none"/></svg></div>

  <div class="review-card" style="left:140px">
    <div class="stars">★★★★★</div>
    <p class="review-text">On the other hand, we denounce with righteous indignation and dislike men who are so beguiled and demoralized by the charms of pleasure of the moment, so blinded by desire, that they cannot foresee the pain and trouble that are bound to ensue; and equal blame belongs to those who fail</p>
    <div class="review-foot"><div class="avatar"></div><div class="reviewer">Maren<small>Irure Dolore</small></div><div class="badge"></div></div>
  </div>
  <div class="review-card" style="left:483px">
    <div class="stars">★★★★★</div>
    <p class="review-text">On the other hand, we denounce with righteous indignation and dislike men who are so beguiled and demoralized by the charms of pleasure of the moment, so blinded by desire, that they cannot foresee the pain and trouble that are bound to ensue; and equal blame belongs to those who fail</p>
    <div class="review-foot"><div class="avatar"></div><div class="reviewer">Maren<small>Irure Dolore</small></div><div class="badge"></div></div>
  </div>
  <div class="review-card" style="left:824px">
    <div class="stars">★★★★★</div>
    <p class="review-text">On the other hand, we denounce with righteous indignation and dislike men who are so beguiled and demoralized by the charms of pleasure of the moment, so blinded by desire, that they cannot foresee the pain and trouble that are bound to ensue; and equal blame belongs to those who fail</p>
    <div class="review-foot"><div class="avatar"></div><div class="reviewer">Maren<small>Irure Dolore</small></div><div class="badge"></div></div>
  </div>
  <div class="review-card" style="left:1165px"></div>
</section>

<section class="blog">
  <h2 class="section-title display" style="top:3091px">Latest Blogs &amp; Updates</h2>

  <article class="blog-card" style="left:105px">
    <div class="blog-img" role="img" aria-label="Shop front with a painted sign and large windows" style="background:linear-gradient(180deg,#c9cdd2,#4f5c6c 50%,#8e9aa6)"></div>
    <h3 class="blog-head">Sed ut perspiciatis unde omnis sit voluptatem accu</h3>
    <p class="blog-body">Lorem ipsum dolor sit amet, consectetur adipiscing elit, sed do eiusmod tempor incididunt ut labore et dolore magna aliqua. Ut enim ad minim veniam, quis nostrud exercitation ullamco</p>
    <a class="blog-link">Read More</a>
  </article>
  <article class="blog-card" style="left:443px">
    <div class="blog-img" role="img" aria-label="Shop floor filled with baskets and dried flowers" style="background:linear-gradient(180deg,#d8d2c8,#8a6c52 55%,#5e4a3a)"></div>
    <h3 class="blog-head">Sed ut perspiciatis unde omnis sit voluptatem accu</h3>
    <p class="blog-body">Lorem ipsum dolor sit amet, consectetur adipiscing elit, sed do eiusmod tempor incididunt ut labore et dolore magna aliqua. Ut enim ad minim veniam, quis nostrud exercitation ullamco</p>
    <a class="blog-link">Read More</a>
  </article>
  <article class="blog-card" style="left:780px">
    <div class="blog-img" role="img" aria-label="Homeware display shelf with glassware and bowls" style="background:linear-gradient(180deg,#6b5a4a,#a79886 55%,#d6d2cc)"></div>
    <h3 class="blog-head">Sed ut perspiciatis unde omnis sit voluptatem accu</h3>
    <p class="blog-body">Lorem ipsum dolor sit amet, consectetur adipiscing elit, sed do eiusmod tempor incididunt ut labore et dolore magna aliqua. Ut enim ad minim veniam, quis nostrud exercitation ullamco</p>
    <a class="blog-link">Read More</a>
  </article>

  <div class="btn btn-sky" style="left:442px;top:3715px">View More</div>
  <div class="btn btn-slate" style="left:607px;top:3715px">Contact Us</div>
</section>

<footer class="footer">
  <div class="abs" style="left:205px;top:80px;width:80px;height:80px;border-radius:50%;background:#3b3b3d"></div>
  <div class="footer-name">quillmoss</div>
  <div class="footer-slogan">LIVE YOUR BEST LIFE</div>

  <div class="footer-col" style="left:460px">
    <h4>Quick Links</h4>
    <ul><li>Home</li><li>About Us</li><li>Products</li><li>Reviews</li><li>Contact Us</li></ul>
  </div>
  <div class="footer-col" style="left:655px">
    <h4>Help Links</h4>
    <ul><li>Get Started</li><li>Blogs</li><li>Support</li><li>Privacy Policy</li><li>Terms Of Use</li></ul>
  </div>
  <div class="footer-col" style="left:847px">
    <h4>Join With Us</h4>
    <p style="font-size:13px">Sed ut perspiciatis unde omnis iste natus</p>
    <div class="field">Email Address</div>
    <div class="subscribe">Subscribe Now</div>
  </div>
</footer>

<div class="bottom-bar">
  <p class="abs" style="left:112px;top:22px;font-size:11px;color:var(--white)">(C) Copyright 2024 | All Rights Reserved</p>
  <span class="social" style="left:992px"></span>
  <span class="social" style="left:1025px"></span>
  <span class="social" style="left:1058px"></span>
</div>

</body>
</html>
```